Marcus Delbridge Finance

Need a personal website advertising Equipment Finance,Business Finance,Commercial Finance, Construction Finance, Bridging Finance. Similar websites are www.corvalend.com.au / www.tarmivest.com.au / www.qbr7.com.au /wwwhalvecredit.com.au

Target Market(s)

Business People

Industry/Entity Type

Business

Number of Pages Required

3 page

Font styles to use
Serif
Sans Serif

Requirements
Must have
• All i want is a simple corporate looking website advertising Equipment Finance, Commercial Finance, Construction Finance, Business Finance, Bridging Finance,

```html
<!DOCTYPE html>
<html lang="en">
<head>
<meta charset="utf-8">
<title>Marcus Delbridge Finance</title>
<link href="https://fonts.googleapis.com/css2?family=Tinos:wght@400;700&family=Open+Sans:wght@400;600&family=Raleway:wght@400&display=swap" rel="stylesheet">
<style>
:root{
  --navy:#1d4f8c;
  --navy-dark:#163e70;
  --navy-deep:#0f2f57;
  --accent:#2a7bc4;
  --ink:#222;
  --muted:#555;
  --line:#d8d8d8;
  --white:#fff;
  --grey-band:#e6e6e6;
  --charcoal:#2f2f2f;
}
*{box-sizing:border-box;margin:0;padding:0}
html,body{width:1200px;height:2594px;overflow:hidden;background:var(--white)}
body{position:relative;font-family:"Open Sans",Arial,sans-serif;color:var(--ink)}
.abs{position:absolute}
.serif{font-family:"Tinos","Times New Roman",serif}

/* header */
.topbar{left:740px;top:0;width:460px;height:38px;background:var(--grey-band);clip-path:polygon(4% 0,100% 0,100% 100%,0 100%)}
.call{left:756px;top:6px;display:flex;align-items:center;gap:10px;font-size:13px;color:#333}
.round{width:26px;height:26px;border-radius:50%;background:var(--navy);display:inline-block}
.socials{left:917px;top:5px;display:flex;gap:5px}
.brand{left:172px;top:72px;font-size:20px;font-weight:700;color:var(--navy);letter-spacing:.5px}
.brand-mark{left:250px;top:22px;width:44px;height:44px;border-radius:50%;background:var(--navy)}
.search{left:790px;top:58px;width:248px;height:37px;display:flex}
.search .field{flex:1;border:1px solid #cfcfcf;font-size:12px;color:#999;padding:10px;font-family:"Tinos",serif}
.search .btn{width:40px;background:var(--navy-dark);display:flex;align-items:center;justify-content:center}
.nav{left:0;top:115px;width:1200px;height:43px;background:linear-gradient(#2a5f9e,#163e70)}
.nav ul{list-style:none;display:flex;gap:26px;padding-left:176px;height:100%;align-items:center}
.nav li{font-family:"Tinos",serif;font-size:14.5px;color:var(--white)}

/* hero */
.hero{left:0;top:158px;width:1200px;height:502px;background:linear-gradient(120deg,#3b4a58 0%,#8aa3b8 40%,#c9d6e0 65%,#5e7184 100%)}
.hero-cap{left:0;top:600px;width:1200px;height:60px;background:rgba(20,25,30,.55);color:var(--white);font-family:"Raleway",sans-serif;font-size:26px;text-align:center;line-height:60px}
.hero-arrow{top:385px;width:22px;height:26px;background:rgba(30,30,30,.8);display:flex;align-items:center;justify-content:center}

/* about */
.about-title{left:0;top:692px;width:1200px;text-align:center;font-size:32px;color:#1a1a1a}
.about-title span{color:var(--accent)}
.rule{left:520px;top:743px;width:160px;height:1px;background:var(--accent)}
.rule b{position:absolute;left:63px;top:-1px;width:34px;height:3px;background:var(--navy)}
.about-text{left:168px;top:778px;width:864px;font-size:10.5px;line-height:17px;text-align:center;color:#333}

/* services */
.services{left:0;top:918px}
.services text{font-family:"Tinos",serif;fill:var(--white)}

/* why */
.why{left:0;top:1407px;width:1200px;height:434px;background:var(--navy);overflow:hidden}
.why h2{position:absolute;left:0;top:42px;width:1200px;text-align:center;color:var(--white);font-family:"Tinos",serif;font-weight:400;font-size:29px}
.why .under{left:540px;top:88px;width:120px;height:1px;background:rgba(255,255,255,.6)}
.point{color:var(--white)}
.point h3{font-family:"Tinos",serif;font-size:16px;font-weight:700;line-height:18px;margin-bottom:4px}
.point p{font-size:11px;line-height:16px}
.point.left{text-align:right}

/* testimonials */
.test-title{left:0;top:1908px;width:1200px;text-align:center;font-size:28px;color:#1a1a1a}
.test-title span{color:var(--navy)}
.quote{left:236px;top:1985px;width:770px;text-align:center;font-style:italic;font-size:13.5px;line-height:26px;color:#333}
.qmark{font-family:"Tinos",serif;font-size:46px;color:#ccc;line-height:1}
.who{left:0;top:2077px;width:1200px;text-align:center}
.who .n{color:var(--navy);font-weight:600;font-size:15px}
.who .l{font-size:13px;color:#333;margin-top:4px}
.dots{left:572px;top:2143px;display:flex;gap:6px}
.dots i{width:8px;height:8px;border-radius:50%;background:#9a9a9a}
.dots i:first-child{background:var(--navy)}

/* newsletter */
.news{left:0;top:2199px;width:1200px;height:66px;background:linear-gradient(#4a4a4a,#1c1c1c)}
.news-title{left:257px;top:2215px;font-size:25px;color:var(--white)}
.news-input{left:660px;top:2213px;width:258px;height:35px;background:var(--white);font-size:11px;padding:11px 10px;color:#333}
.news-btn{left:918px;top:2213px;width:122px;height:35px;background:var(--navy);color:var(--white);font-size:12.5px;text-align:center;line-height:35px;letter-spacing:.5px}

/* footer */
.footer{left:0;top:2265px;width:1200px;height:284px;background:linear-gradient(#1d5599,#17467f)}
.fdiv{top:2300px;width:1px;height:230px;background:rgba(255,255,255,.2)}
.fh{top:2310px;font-family:"Tinos",serif;font-size:17px;color:var(--white)}
.fh-line{top:2338px;height:1px;background:rgba(255,255,255,.25)}
.links{left:165px;top:2352px;list-style:none}
.links li{font-family:"Tinos",serif;font-size:12.5px;color:var(--white);line-height:22.5px}
.links li::before{content:"› ";}
.contact{left:358px;top:2350px;color:var(--white);font-family:"Tinos",serif;font-size:12.5px}
.contact .row{display:flex;gap:10px;margin-bottom:14px;line-height:17px}
.contact .ic{width:18px;height:18px;border-radius:50%;background:var(--white);flex:none;margin-top:1px}
.inp{left:608px;width:207px;background:var(--white);font-size:11px;padding:9px 8px;color:#333}
.submit{left:608px;top:2495px;width:103px;height:33px;background:#0b0b0b;color:var(--white);font-family:"Tinos",serif;font-size:15px;line-height:33px;padding-left:12px}
.fsocial{left:857px;top:2354px;display:flex;gap:6px}
.fsocial i{width:30px;height:30px;border-radius:50%;background:var(--white);border:2px solid #cfd9e6}
.copy{left:0;top:2549px;width:1200px;height:45px;background:var(--charcoal);color:#ddd;font-family:"Tinos",serif;font-size:12.5px;text-align:center;line-height:45px}
</style>
</head>
<body>

<header>
  <div class="abs topbar"></div>
  <div class="abs call"><span class="round"></span>Call : 555-018-2046</div>
  <div class="abs socials"><span class="round"></span><span class="round"></span><span class="round"></span><span class="round"></span></div>
  <div class="abs brand-mark"></div>
  <div class="abs brand serif">MARCUS DELBRIDGE FINANCE</div>
  <div class="abs search"><div class="field">Search here...</div><div class="btn">
    <svg width="16" height="16" viewBox="0 0 16 16"><circle cx="6.5" cy="6.5" r="5" fill="none" stroke="#fff" stroke-width="2"/><line x1="10" y1="10" x2="15" y2="15" stroke="#fff" stroke-width="2.4"/></svg></div></div>
  <nav class="abs nav"><ul>
    <li>Home</li><li>Equipment Finance</li><li>Business Finance</li><li>Commercial Finance</li><li>Construction Finance</li><li>Bridging Finance</li><li>Contact Us</li>
  </ul></nav>
</header>

<section>
  <div class="abs hero" role="img" aria-label="Office scene with business people talking beside a laptop"></div>
  <div class="abs hero-cap">Focus on What you do Best, While We take care of your finances</div>
  <div class="abs hero-arrow" style="left:6px"><svg width="8" height="12"><path d="M7 1 2 6l5 5" fill="none" stroke="#fff" stroke-width="2"/></svg></div>
  <div class="abs hero-arrow" style="left:1162px"><svg width="8" height="12"><path d="M1 1l5 5-5 5" fill="none" stroke="#fff" stroke-width="2"/></svg></div>
</section>

<section>
  <h1 class="abs about-title serif" style="font-weight:400">About Marcus Delbridge <span>- Finance</span></h1>
  <div class="abs rule"><b></b></div>
  <p class="abs about-text">Lorem ipsum dolor sit amet, consectetuer adipiscing elit, sed diam nonummy nibh euismod tincidunt ut laoreet dolore magna aliquam erat volutpat. Ut wisi enim ad minim veniam, quis nostrud exerci tation ullamcorper suscipit lobortis nisl ut aliquip ex ea commodo consequat. Duis autem vel eum iriure dolor in hendrerit in vulputate velit esse molestie consequat, vel illum dolore eu feugiat nulla facilisis at vero eros et accumsan et iusto odio dignissim qui blandit praesent. Ut wisi enim ad minim veniam, quis nostrud exerci tation ullamcorper suscipit lobortis nisl ut aliquip ex ea commodo consequat. Duis autem vel eum iriure dolor in hendrerit in vulputate velit esse molestie luptatum zzril delenit augue duis dolore te feugait nulla facilisi.</p>
</section>

<section class="abs services">
  <svg width="1200" height="450" viewBox="0 0 1200 450">
    <defs>
      <path id="hex" d="M0-115 100-57.5 100 57.5 0 115-100 57.5-100-57.5Z"/>
    </defs>
    <g stroke="#dcdcdc" stroke-width="9" stroke-linejoin="round">
      <use href="#hex" x="375" y="122" fill="#5d6e80" role="img" aria-label="Excavator at a construction site"/>
      <use href="#hex" x="600" y="122" fill="#1d4f8c"/>
      <use href="#hex" x="825" y="122" fill="#8ea6bf" role="img" aria-label="Hands reviewing financial charts"/>
      <use href="#hex" x="263" y="322" fill="#6b7f96" role="img" aria-label="Business handshake"/>
      <use href="#hex" x="488" y="322" fill="#7d8c9c" role="img" aria-label="Building under construction with cranes"/>
      <use href="#hex" x="712" y="322" fill="#8d8f93" role="img" aria-label="Balanced stones"/>
      <use href="#hex" x="935" y="322" fill="#a9b3bf" role="img" aria-label="Person signing documents"/>
    </g>
    <line x1="545" y1="135" x2="655" y2="135" stroke="#fff" stroke-opacity=".6"/>
    <text x="600" y="115" text-anchor="middle" font-size="38">Our</text>
    <text x="600" y="156" text-anchor="middle" font-size="38">Services</text>
    <g font-size="17" text-anchor="middle">
      <text x="380" y="188">Equipment Finance</text>
      <text x="835" y="193">Business Finance</text>
      <text x="259" y="386">Commercial Finance</text>
      <text x="493" y="386">Construction Finance</text>
      <text x="723" y="384">Bridging Finance</text>
      <text x="935" y="386">Others</text>
    </g>
  </svg>
</section>

<section class="abs why">
  <h2>Why Choose Us</h2>
  <div class="abs under"></div>
  <svg class="abs" style="left:0;top:0" width="1200" height="434" viewBox="0 0 1200 434">
    <circle cx="600" cy="465" r="165" fill="#fff"/>
    <circle cx="600" cy="465" r="194" fill="none" stroke="#3f7ad0" stroke-width="5"/>
    <g stroke="#fff" stroke-dasharray="3 3" stroke-width="1.5">
      <line x1="379" y1="360" x2="447" y2="362"/><line x1="432" y1="258" x2="484" y2="309"/>
      <line x1="536" y1="204" x2="558" y2="268"/><line x1="662" y1="204" x2="642" y2="268"/>
      <line x1="766" y1="258" x2="716" y2="309"/><line x1="820" y1="360" x2="753" y2="362"/>
    </g>
    <g fill="#fff" stroke="#1d4f8c" stroke-width="2">
      <circle cx="447" cy="362" r="6"/><circle cx="484" cy="309" r="6"/><circle cx="558" cy="268" r="6"/>
      <circle cx="642" cy="268" r="6"/><circle cx="716" cy="309" r="6"/><circle cx="753" cy="362" r="6"/>
    </g>
    <g fill="#fff">
      <circle cx="379" cy="360" r="36"/><circle cx="432" cy="258" r="36"/><circle cx="536" cy="204" r="36"/>
      <circle cx="662" cy="204" r="36"/><circle cx="766" cy="258" r="36"/><circle cx="820" cy="360" r="36"/>
    </g>
    <g fill="#1d4f8c">
      <circle cx="379" cy="355" r="10"/><rect x="374" y="367" width="10" height="6"/>
      <circle cx="432" cy="258" r="11"/><circle cx="432" cy="258" r="4" fill="#fff"/>
      <path d="M522 192c3-3 7 2 6 5l-3 3c2 5 6 9 11 11l3-3c3-1 8 3 5 6-4 5-10 4-16-1s-10-14-6-21z"/>
      <circle cx="662" cy="196" r="9"/><path d="M646 222a16 12 0 0 1 32 0z"/>
      <rect x="752" y="246" width="28" height="24" rx="2"/><rect x="756" y="254" width="20" height="12" fill="#fff"/>
      <circle cx="812" cy="352" r="7"/><circle cx="828" cy="352" r="7"/><path d="M802 372a10 8 0 0 1 36 0z"/>
    </g>
    <text x="600" y="420" text-anchor="middle" font-family="Tinos,serif" font-weight="700" font-size="20" fill="#1d4f8c">MARCUS DELBRIDGE FINANCE</text>
  </svg>
  <div class="abs point left" style="right:721px;top:123px"><h3>Unbiased Recommendations</h3><p>Lorem ipsum dolor sit mork<br>[+]...adipiscing sed diam</p></div>
  <div class="abs point left" style="right:826px;top:208px"><h3>Unparalleled<br>Service</h3><p>Lorem ipsum dolor sit mork<br>[+]...adipiscing sed diam</p></div>
  <div class="abs point left" style="right:878px;top:337px"><h3>Superior Advice</h3><p>Lorem ipsum dolor sit mork<br>[+]...adipiscing sed diam</p></div>
  <div class="abs point" style="left:721px;top:123px"><h3>Expert Guidance</h3><p>Lorem ipsum dolor sit mork<br>adipiscing sed diam...[+]</p></div>
  <div class="abs point" style="left:826px;top:222px"><h3>Considerable Time<br>For You</h3><p>Lorem ipsum dolor sit mork<br>adipiscing sed diam...[+]</p></div>
  <div class="abs point" style="left:878px;top:320px"><h3>Deep Legal Industry<br>Relationships</h3><p>Lorem ipsum dolor sit mork<br>adipiscing sed diam...[+]</p></div>
</section>

<section>
  <h2 class="abs test-title serif" style="font-weight:400">Clients <span>Testimonials</span></h2>
  <div class="abs qmark" style="left:195px;top:1978px">&ldquo;</div>
  <div class="abs qmark" style="left:770px;top:2035px">&rdquo;</div>
  <p class="abs quote">Lorem ipsum dolor sit amet, consectetuer adipiscing elit, sed diam nonummy nibh euismod tinciduntol ut laoreet dolore magna aliquam erat volutpat. Ut wisi enim ad minim veniam, quis nostrud exercimori mornkle tation ullamcorper suscipit lobortis nisl ut aliquip ex ea commodo consequat.</p>
  <div class="abs who"><div class="n">Renata V.</div><div class="l">Harlow Ridge, CA</div></div>
  <div class="abs dots"><i></i><i></i><i></i><i></i></div>
  <svg class="abs" style="left:133px;top:2007px" width="26" height="48"><path d="M24 2 2 24l22 22" fill="none" stroke="#aaa" stroke-width="1.5"/></svg>
  <svg class="abs" style="left:1040px;top:2007px" width="26" height="48"><path d="M2 2l22 22L2 46" fill="none" stroke="#aaa" stroke-width="1.5"/></svg>
</section>

<section>
  <div class="abs news"></div>
  <svg class="abs" style="left:163px;top:2208px" width="78" height="48" viewBox="0 0 78 48">
    <g fill="none" stroke="#fff" stroke-width="2.5"><rect x="22" y="6" width="50" height="34" rx="2"/><path d="M22 6l25 20 25-20"/><line x1="2" y1="22" x2="16" y2="22"/><line x1="6" y1="30" x2="16" y2="30"/><line x1="10" y1="38" x2="16" y2="38"/></g>
  </svg>
  <div class="abs news-title serif">Subscribe Our Newsletter</div>
  <svg class="abs" style="left:570px;top:2220px" width="74" height="26"><path d="M2 20c20 6 45 2 68-14m0 0-9 1m9-1-3 8" fill="none" stroke="#fff" stroke-width="1.5"/></svg>
  <div class="abs news-input">Enter Your Email Address</div>
  <div class="abs news-btn">SUBSCRIBE</div>
</section>

<footer>
  <div class="abs footer"></div>
  <div class="abs fdiv" style="left:338px"></div>
  <div class="abs fdiv" style="left:587px"></div>
  <div class="abs fdiv" style="left:830px"></div>
  <div class="abs fh" style="left:165px">Quick Links</div>
  <div class="abs fh-line" style="left:165px;width:150px"></div>
  <div class="abs fh" style="left:361px">Contact Details</div>
  <div class="abs fh-line" style="left:361px;width:205px"></div>
  <div class="abs fh" style="left:608px">Quick Inquiry</div>
  <div class="abs fh-line" style="left:608px;width:205px"></div>
  <div class="abs fh" style="left:851px">Follow Us</div>
  <div class="abs fh-line" style="left:851px;width:180px"></div>
  <ul class="abs links">
    <li>Home</li><li>Equipment Finance</li><li>Business Finance</li><li>Commercial Finance</li><li>Construction Finance</li><li>Bridging Finance</li><li>Contact Us</li>
  </ul>
  <div class="abs contact">
    <div class="row"><span class="ic"></span><span>Marcus Delbridge Finance<br>Street Name City Name<br>State Zipcode</span></div>
    <div class="row"><span class="ic"></span><span>555-018-2046</span></div>
    <div class="row"><span class="ic"></span><span>555-018-2046</span></div>
    <div class="row"><span class="ic"></span><span>inquiry@delbridgefinance.com</span></div>
  </div>
  <div class="abs inp" style="top:2353px;height:31px">Name</div>
  <div class="abs inp" style="top:2390px;height:31px">Email</div>
  <div class="abs inp" style="top:2426px;height:63px">Message</div>
  <div class="abs submit">Submit &nbsp;&rarr;</div>
  <div class="abs fsocial"><i></i><i></i><i></i><i></i></div>
  <div class="abs copy">Copyright &copy; 2017 Marcus Delbridge Finance. All Rights Reserved.</div>
</footer>

</body>
</html>
```